Design a New Business Card for Our Company

We are looking for fresh, unique, and a modern business card that reflects our roots as digital marketing agency focused on SEM.

Industry/Entity Type

Marketing

Contact Information for Business Card

looking for very unique out of the box designs. clean and modern that compliments our logo

Requirements
Must have
• colors should match our logo
• Front should have name, address, email, and phone/fax of the person, phone/fax are the same number
• back should have our url

```html
<!DOCTYPE html>
<html lang="en">
<head>
<meta charset="utf-8">
<title>Brightpath Studio – Business Card</title>
<link rel="stylesheet" href="https://fonts.googleapis.com/css2?family=Montserrat:wght@400;500;600;700&display=swap">
<style>
  :root {
    --page: #2b2b2d;
    --card: #050505;
    --blue: #5b9bd8;
    --grey: #c4c4c4;
    --text-light: #d9d9d9;
    --text-dim: #bdbdbd;
  }
  * { box-sizing: border-box; margin: 0; padding: 0; }
  html, body { width: 1200px; height: 900px; overflow: hidden; }
  body {
    background: var(--page);
    font-family: "Montserrat", sans-serif;
    position: relative;
  }
  .card {
    position: absolute;
    left: 260px;
    width: 680px;
    height: 390px;
    background: var(--card);
    border-radius: 24px;
    overflow: hidden;
    box-shadow: 0 14px 30px rgba(0,0,0,.45);
  }
  .card--back { top: 40px; }
  .card--front { top: 470px; }
  .card__bands { position: absolute; inset: 0; }

  /* back */
  .brand-center {
    position: absolute;
    top: 140px; left: 0; right: 0;
    display: flex; align-items: center; justify-content: center; gap: 18px;
  }
  .brand-dot {
    width: 54px; height: 54px; border-radius: 50%;
    background: var(--blue);
    flex: none;
  }
  .brand-center .brand-name {
    font-size: 40px; font-weight: 700; color: var(--grey); letter-spacing: -0.5px;
  }
  .back-url {
    position: absolute; left: 34px; bottom: 12px;
    color: #fff; font-size: 17px; font-weight: 500;
  }

  /* front */
  .brand-corner {
    position: absolute; top: 156px; left: 40px;
    display: flex; align-items: center; gap: 12px;
  }
  .brand-corner .brand-dot { width: 34px; height: 34px; }
  .brand-corner .brand-name {
    font-size: 34px; font-weight: 700; color: var(--grey); letter-spacing: -0.5px;
    white-space: nowrap;
  }
  .person {
    position: absolute; top: 46px; right: 40px; text-align: right;
  }
  .person__name { color: var(--blue); font-size: 27px; font-weight: 700; }
  .person__title { color: var(--text-light); font-size: 15px; margin-top: 2px; }
  .person__rule {
    height: 2px; background: var(--blue); width: 300px; margin: 10px 0 12px auto;
  }
  .person__address { color: var(--text-light); font-size: 17px; line-height: 1.35; }

  .contact {
    position: absolute; left: 40px; bottom: 36px;
    list-style: none;
  }
  .contact::before {
    content: ""; display: block;
    width: 300px; height: 2px; background: var(--blue); margin-bottom: 10px;
  }
  .contact li {
    display: flex; align-items: center; gap: 12px;
    color: var(--text-light); font-size: 17px; line-height: 1.4;
    white-space: nowrap;
  }
  .contact svg { width: 15px; height: 15px; flex: none; fill: none; stroke: var(--text-dim); stroke-width: 2; }
  .contact .accent { color: var(--blue); font-weight: 600; }
</style>
</head>
<body>

<section class="card card--back" aria-label="Card back">
  <svg class="card__bands" viewBox="0 0 680 390" preserveAspectRatio="none">
    <polygon points="0,352 680,352 680,364 0,364" fill="var(--grey)"/>
    <polygon points="0,330 380,330 420,364 0,364" fill="var(--blue)"/>
    <rect x="0" y="364" width="680" height="26" fill="var(--blue)"/>
  </svg>
  <div class="brand-center">
    <span class="brand-dot"></span>
    <span class="brand-name">Brightpath Studio</span>
  </div>
  <p class="back-url">www.brightpathstudio.com</p>
</section>

<section class="card card--front" aria-label="Card front">
  <svg class="card__bands" viewBox="0 0 680 390" preserveAspectRatio="none">
    <polygon points="470,252 680,252 680,320 440,320" fill="var(--blue)"/>
    <polygon points="0,372 680,372 680,390 0,390" fill="var(--grey)"/>
  </svg>
  <div class="brand-corner">
    <span class="brand-dot"></span>
    <span class="brand-name">Brightpath Studio</span>
  </div>
  <div class="person">
    <p class="person__name">Marlo Jensen</p>
    <p class="person__title">Director</p>
    <div class="person__rule"></div>
    <p class="person__address">PO Box 417 Riverton<br>NSW Australia 2091</p>
  </div>
  <ul class="contact">
    <li><svg viewBox="0 0 16 16"><path d="M3 2l3 1 1 3-2 1a8 8 0 0 0 4 4l1-2 3 1 1 3-2 1C7 14 2 9 2 4z"/></svg><span>+330 1470-3321</span></li>
    <li><svg viewBox="0 0 16 16"><rect x="2" y="6" width="12" height="6"/><rect x="4" y="2" width="8" height="4"/><rect x="4" y="10" width="8" height="4"/></svg><span>+330 1590-6642</span></li>
    <li><svg viewBox="0 0 16 16"><rect x="2" y="3" width="12" height="10"/><path d="M2 3l6 5 6-5"/></svg><span>info@brightpathstudio.com</span></li>
    <li><svg viewBox="0 0 16 16"><circle cx="8" cy="8" r="6"/><path d="M2 8h12M8 2c3 3 3 9 0 12M8 2c-3 3-3 9 0 12"/></svg><span>www.<span class="accent">brightpathstudio</span>.com</span></li>
  </ul>
</section>

</body>
</html>
```